Accounting firm needing business card / letterhead designed
Marcus L. Trenholm, CPA
marcus@veltrowledger.com
www.veltrowledger.com
842 E Alder Ave Corvale, IN 43827
419-562-0974

```html
<!DOCTYPE html>
<html lang="en">
<head>
<meta charset="utf-8">
<title>Veltrow Ledger — Business Card</title>
<link href="https://fonts.googleapis.com/css2?family=Roboto:wght@400;500&family=Roboto+Condensed:wght@700&display=swap" rel="stylesheet">
<style>
  :root{
    --navy:#27255f;
    --green:#82bf3a;
    --paper:#f4f4f3;
    --ink:#4a4a4a;
    --rule:#3a3a3a;
    --backdrop:#e6e3de;
    --white:#ffffff;
  }
  *{margin:0;padding:0;box-sizing:border-box}
  html,body{width:1200px;height:960px;overflow:hidden}
  body{background:var(--backdrop);position:relative;font-family:"Roboto",Arial,sans-serif}

  .card{position:absolute;height:343px;box-shadow:0 2px 6px rgba(0,0,0,.18)}
  .card-front{left:315px;top:113px;width:627px;background:var(--paper)}
  .card-back{left:311px;top:472px;width:600px;background:var(--green)}

  .wordmark{position:absolute;left:0;right:0;text-align:center;
    font-family:"Roboto",Arial,sans-serif;font-weight:500;letter-spacing:3px;white-space:nowrap}
  .card-front .wordmark{top:66px;font-size:46px;color:var(--navy)}
  .card-back .wordmark{top:124px;font-size:46px;color:var(--white)}

  .divider{position:absolute;left:38px;top:222px;width:519px;height:1px;background:var(--rule)}
  .divider-accent{position:absolute;left:38px;top:221px;width:187px;height:5px;background:var(--green)}

  .holder{position:absolute;left:38px;top:244px}
  .holder-name{font-family:"Roboto Condensed",Arial,sans-serif;font-weight:700;font-size:20px;color:var(--navy);line-height:1.2}
  .holder-address{margin-top:6px;font-size:14px;color:var(--ink);line-height:18px}

  .contact{position:absolute;right:66px;top:252px;list-style:none;text-align:right;font-size:14px;color:var(--ink);line-height:19px}
  .contact li{display:flex;align-items:center;justify-content:flex-end;gap:7px}
  .contact svg{width:13px;height:13px;fill:var(--navy);flex:none}

  .back-url{position:absolute;left:0;right:0;top:283px;text-align:center;color:var(--white);
    font-size:13px;letter-spacing:5.5px}
</style>
</head>
<body>

<section class="card card-front">
  <div class="wordmark">VELTROW LEDGER</div>
  <div class="divider"></div>
  <div class="divider-accent"></div>
  <div class="holder">
    <div class="holder-name">Marcus L. Trenholm, CPA</div>
    <div class="holder-address">842 E Alder Ave<br>Corvale, IN 43827</div>
  </div>
  <ul class="contact">
    <li>419-562-0974
      <svg viewBox="0 0 24 24" aria-hidden="true"><path d="M6.6 10.8a15.1 15.1 0 0 0 6.6 6.6l2.2-2.2c.3-.3.7-.4 1-.2 1.1.4 2.3.6 3.6.6.6 0 1 .4 1 1V20c0 .6-.4 1-1 1A17 17 0 0 1 3 4c0-.6.4-1 1-1h3.5c.6 0 1 .4 1 1 0 1.3.2 2.5.6 3.6.1.3 0 .7-.2 1z"/></svg>
    </li>
    <li>marcus@veltrowledger.com
      <svg viewBox="0 0 24 24" aria-hidden="true"><path d="M2 5h20v14H2z"/><path d="M3 6l9 7 9-7" fill="none" stroke="#f4f4f3" stroke-width="1.6"/></svg>
    </li>
    <li>www.veltrowledger.com
      <svg viewBox="0 0 24 24" aria-hidden="true"><circle cx="12" cy="12" r="10"/><path d="M2 12h20M12 2c3 3 3 17 0 20M12 2c-3 3-3 17 0 20" fill="none" stroke="#f4f4f3" stroke-width="1.4"/></svg>
    </li>
  </ul>
</section>

<section class="card card-back">
  <div class="wordmark">VELTROW LEDGER</div>
  <div class="back-url">www.veltrowledger.com</div>
</section>

</body>
</html>
```